Website design for Puddle Jump Kidscare

I need a website designed for my daycare business, Puddle Jump Kidscare, now that I have a new logo. My former website was ok but simple and I did not have a logo yet. It also was created by me using a template and was entirely pink. I loved the bright, happy feel of it but worried it might not appeal as much to potential clients who have sons. Therefore, I need a site which will appeal to both genders while still keeping the cheerful color scheme of my new logo, which has pinks, blue, green and cream.
Updates

Reason: Hello! I am still trying to download my new logo and am sorry it is taking me so long. Hopefully I will it posted by the end of today (US Eastern Standard Time). Thank you all very much for your patience!

Hello! I have finally managed to upload my new logo for you to use in designing my website. I'm sorry it took so long and greatly appreciate your time and creative efforts! I look forward to seeing what is submitted based on my logo design and its style/colors.

Many thanks!

Reason: As I've been traveling and posted my logo file late, I am extending my deadline. I am now back and can focus on providing more and better feedback. I appreciate your patience and submissions very much!

Reason: I need more time to provide feedback and make decisions.

Industry/Entity Type

Daycare

Colors
0192cd
33a6d7
86cae7
cadf82
fbf289
add136
e34197

```html
<!DOCTYPE html>
<html lang="en">
<head>
<meta charset="utf-8">
<title>Puddle Jump Kidscare</title>
<link href="https://fonts.googleapis.com/css2?family=Open+Sans:wght@300;400;600&family=Signika:wght@600&display=swap" rel="stylesheet">
<style>
:root{
  --pink:#e8689a;
  --pink-dark:#e35d91;
  --pink-pale:#fde3ee;
  --green:#97c11f;
  --blue:#3aaee0;
  --text:#777;
  --dark:#333;
  --cream:#fcf5ee;
  --border:#ddd;
}
*{margin:0;padding:0;box-sizing:border-box}
html,body{width:1014px;height:1200px;overflow:hidden;background:#fff}
body{font-family:"Open Sans",Arial,sans-serif;color:var(--text);position:relative}
.header{position:absolute;top:0;left:0;width:1014px;height:109px;background:linear-gradient(#fcc3dc,var(--pink-pale));border-top:4px dotted #fff}
.brand{position:absolute;left:86px;top:20px;font-size:31px;line-height:37px;color:#f08ab6;text-align:center;font-weight:400}
.nav{position:absolute;top:109px;left:0;width:1014px;height:50px;background:linear-gradient(#f49cc1,var(--pink-dark));display:flex;padding-left:70px}
.nav a{color:#fff;text-decoration:none;font-size:14px;line-height:50px;padding:0 21.5px;border-right:1px solid rgba(255,255,255,.35)}
.nav a:last-child{border-right:none}
.hero{position:absolute;top:159px;left:0;width:1014px;height:414px;background:linear-gradient(#cfe8f6 0%,#eef7fc 35%,#f3d7e3 52%,#e8c86a 62%,#8fcf4a 76%,#5fae2a 100%)}
.hero-badge{position:absolute;left:72px;top:35px;width:338px;height:338px;border-radius:50%;background:rgba(173,209,54,.88);text-align:center;color:#fff}
.hero-badge::after{content:"";position:absolute;inset:10px;border-radius:50%;border:4px dotted rgba(255,255,255,.7)}
.hero-title{font-family:"Signika",sans-serif;font-size:40px;line-height:44px;padding-top:108px;letter-spacing:1px}
.hero-sub{font-family:"Signika",sans-serif;font-size:21px;line-height:24px;margin-top:4px}
.hero-text{font-size:11px;line-height:16.5px;margin:8px auto 0;width:240px}
.dots{position:absolute;top:390px;left:473px;display:flex;gap:4px}
.dots span{width:14px;height:14px;border-radius:50%;background:#fff}
.features{position:absolute;top:595px;left:62px;width:889px;height:148px;border:1px solid var(--border);display:flex;background:linear-gradient(#fff 70%,#f6f6f6)}
.feature{flex:1;position:relative;border-right:1px solid var(--border)}
.feature:last-child{border-right:none}
.feature-img{position:absolute;left:16px;top:14px;width:82px;height:114px;border-radius:2px}
.feature h2{position:absolute;left:112px;top:17px;font-size:21px;font-weight:400}
.feature p{position:absolute;left:112px;top:46px;width:175px;font-size:11.3px;line-height:17.5px}
.btn{position:absolute;left:112px;top:105px;width:90px;height:26px;border-radius:2px;color:#fff;font-size:10.5px;line-height:26px;text-align:center}
.learning h2{color:var(--green)}.learning .btn{background:var(--green)}
.creativity h2{color:var(--pink)}.creativity .btn{background:var(--pink)}
.sharing h2{color:var(--blue)}.sharing .btn{background:var(--blue)}
.welcome{position:absolute;top:787px;left:62px;width:578px}
.welcome h1{font-size:28px;font-weight:400;color:var(--pink);line-height:34px}
.welcome h3{font-size:19.5px;font-weight:300;color:var(--pink);margin-bottom:11px}
.welcome p{font-size:11.2px;line-height:19px;margin-bottom:9px}
.news{position:absolute;top:793px;left:668px;width:280px}
.news h2{font-size:25px;font-weight:300;color:var(--dark);margin-bottom:14px}
.news-item{display:flex;gap:12px;margin-bottom:37px}
.news-img{width:88px;height:65px;flex:none}
.news-item h4{font-size:13.5px;font-weight:400;color:var(--blue);line-height:17px;margin-bottom:2px}
.news-item p{font-size:10.3px;line-height:17.3px}
.footer{position:absolute;top:1102px;left:0;width:1014px;height:98px;background:var(--cream);border-top:1px solid #ece4dc}
.footer-nav{position:absolute;left:64px;top:26px;font-size:12.5px;color:var(--dark)}
.footer-nav span{margin:0 8px;color:#555}
.copyright{position:absolute;left:64px;top:55px;font-size:11.5px;color:#888}
</style>
</head>
<body>
<header class="header"><div class="brand">Puddle Jump<br>Kidscare</div></header>
<nav class="nav">
  <a>HOME</a><a>ABOUT</a><a>SERVICES</a><a>HOURS &amp; FEES</a><a>POLICIES</a><a>TESTIMONIALS</a><a>PHOTOS</a><a>CONTACT</a>
</nav>
<section class="hero" role="img" aria-label="Five smiling children lying on green grass under a bright sky">
  <div class="hero-badge">
    <div class="hero-title">PLAYSCAPE</div>
    <div class="hero-sub">WHERE CHILDREN CAN PLAY</div>
    <p class="hero-text">Maecenas at justo id velit placerat molestie Donec dictum lectus non odio Cras a ante vitae enim iaculis aliquam</p>
  </div>
  <div class="dots"><span></span><span></span><span></span></div>
</section>
<section class="features">
  <div class="feature learning">
    <div class="feature-img" role="img" aria-label="Boy sitting beside a stack of books" style="background:linear-gradient(#f4f4f4,#d9d4cc)"></div>
    <h2>LEARNING</h2>
    <p>Mauris vel lacus vitae felis ves-tibulum volutpat Etiam est nunc venenatis in tristique eu</p>
    <div class="btn">READ MORE</div>
  </div>
  <div class="feature creativity">
    <div class="feature-img" role="img" aria-label="Children in colourful clown costumes" style="background:linear-gradient(#f7e7b5,#e6a4b5)"></div>
    <h2>CREATIVITY</h2>
    <p>Mauris vel lacus vitae felis ves-tibulum volutpat Etiam est nunc venenatis in tristique eu</p>
    <div class="btn">READ MORE</div>
  </div>
  <div class="feature sharing">
    <div class="feature-img" role="img" aria-label="Golden star trophy" style="background:linear-gradient(#f7efd9,#c9a870)"></div>
    <h2>SHARING</h2>
    <p>Mauris vel lacus vitae felis ves-tibulum volutpat Etiam est nunc venenatis in tristique eu</p>
    <div class="btn">READ MORE</div>
  </div>
</section>
<section class="welcome">
  <h1>Welcome to Puddle Jump Kidscare,</h1>
  <h3>a playspace where children can play, create, and imagine!</h3>
  <p>Welcome to Puddle Jump Kidscare, a licensed Group Family Day Care, located in Brookfield's leafy Riverside district. We are located on a pretty, tree-lined block on Linden Lane, between Oak and Elm Avenues. We are a few blocks from the Green Line tram and the Harbor Road bus route, and we offer flexible hourly childcare, making it as easy as possible for busy parents on the go to arrange their children's care.</p>
  <p>We invite you to learn more about us and hope you will visit us soon!</p>
  <p>Etiam eu urna Sed porta Suspendisse quam leo molestie sed luctus quis feugiat in pede Fusce tellus Sed metus augue convallis et vehicula ut pulvinar eu ante Integer orci tellus tristique vitae consequat nec porta vel lectus Nulla sit amet diam Duis non nunclibero a tempus libero lectus</p>
</section>
<aside class="news">
  <h2>Latest News</h2>
  <div class="news-item">
    <div class="news-img" role="img" aria-label="Teacher helping children with drawing" style="background:linear-gradient(135deg,#c9dbe8,#e3b98f)"></div>
    <div><h4>Praesent vitae lacus</h4><p>Maecenas at justo id velit placerat molestie Donec dictum lectus non odio Cras a ante vitae enim</p></div>
  </div>
  <div class="news-item">
    <div class="news-img" role="img" aria-label="Young children painting at a table" style="background:linear-gradient(135deg,#f3d27a,#8cc7dc)"></div>
    <div><h4>Suspendisse quam leo</h4><p>Maecenas at justo id velit placerat molestie Donec dictum lectus non odio Cras a ante vitae enim</p></div>
  </div>
</aside>
<footer class="footer">
  <div class="footer-nav">HOME<span>|</span>ABOUT<span>|</span>SERVICES<span>|</span>HOURS &amp; FEES<span>|</span>POLICIES<span>|</span>TESTIMONIALS<span>|</span>PHOTOS<span>|</span>CONTACT</div>
  <div class="copyright">Copyright © 2014 Company Name. All right reserved</div>
</footer>
</body>
</html>
```